Redesign of business card for Cedar Ridge Mechanical

We are looking for a new design for our business cards for Cedar Ridge Mechanical. We are a plumbing & HVAC construction company, operating on the West Coast of Canada and USA. Logo attached.
Industry/Entity Type
Construction - Plumbing & HVAC
Contact Information for Business Card
Name, address, phone numbers, email, website address
Look and feel
Each slider illustrates characteristics of the customer's brand and the style your logo design should communicate.

```html
<!DOCTYPE html>
<html lang="en">
<head>
<meta charset="UTF-8">
<title>Cedar Ridge Mechanical – Business Card</title>
<link href="https://fonts.googleapis.com/css2?family=Montserrat:wght@400;600;700&display=swap" rel="stylesheet">
<style>
  :root {
    --stage: #2a2c30;
    --card-black: #1b1b1c;
    --card-white: #ffffff;
    --ink-white: #f2f2f2;
    --ink-grey: #a9a9a9;
    --ink-black: #111111;
    --spot-gloss: #3c3c3e;
  }
  * { box-sizing: border-box; margin: 0; padding: 0; }
  html, body {
    width: 1200px; height: 900px; overflow: hidden;
    background: var(--stage);
    font-family: "Montserrat", sans-serif;
  }
  .canvas {
    position: relative; width: 1200px; height: 900px;
    display: flex; flex-direction: column; align-items: center; justify-content: center; gap: 60px;
  }
  .card {
    position: relative; width: 525px; height: 300px;
    border-radius: 26px; overflow: hidden;
    background: var(--card-black);
  }
  .card-front .curve-art { position: absolute; inset: 0; }
  .contact-block {
    position: absolute; left: 42px; top: 40px; color: var(--ink-white);
  }
  .person-name { font-weight: 700; font-size: 21px; letter-spacing: 0.2px; }
  .person-role { font-size: 11px; color: var(--ink-grey); margin-top: 3px; }
  .address { font-size: 12px; line-height: 1.45; margin-top: 30px; color: var(--ink-white); }
  .contact-list { list-style: none; margin-top: 10px; font-size: 12px; line-height: 1.9; }
  .contact-list li { display: flex; align-items: center; gap: 10px; }
  .contact-list svg { width: 11px; height: 11px; flex: none; }
  .brand-mark {
    position: absolute; display: flex; align-items: center; gap: 10px;
    font-weight: 600; text-transform: uppercase; letter-spacing: 0.5px;
  }
  .card-front .brand-mark {
    right: 26px; top: 50%; transform: translateY(-50%);
    width: 190px; font-size: 17px; line-height: 1.2; color: var(--ink-black);
  }
  .brand-square { flex: none; width: 18px; height: 18px; background: currentColor; }
  .card-back .brand-mark {
    left: 50%; top: 50%; transform: translate(-50%, -50%);
    font-size: 24px; color: var(--spot-gloss); white-space: nowrap;
  }
  .card-back .brand-square { width: 22px; height: 22px; }
</style>
</head>
<body>
<main class="canvas">
  <section class="card card-front">
    <svg class="curve-art" viewBox="0 0 525 300" aria-hidden="true">
      <path d="M340 0 C262 70 250 220 305 300 L525 300 L525 0 Z" fill="var(--card-white)"/>
      <path d="M312 0 C270 38 246 88 236 150" fill="none" stroke="var(--card-white)" stroke-width="4" stroke-linecap="round"/>
    </svg>
    <div class="contact-block">
      <p class="person-name">Daniel Hart</p>
      <p class="person-role">Managing Director</p>
      <p class="address">48 Harbor View Road<br>Fairhaven, WA 98225</p>
      <ul class="contact-list">
        <li><svg viewBox="0 0 12 12"><path d="M2.5 1 L4.5 1 L5.2 3.4 L4 4.4 C4.6 5.8 6.2 7.4 7.6 8 L8.6 6.8 L11 7.5 L11 9.5 C11 10.3 10.3 11 9.5 11 C5 11 1 7 1 2.5 C1 1.7 1.7 1 2.5 1 Z" fill="var(--ink-white)"/></svg>888.555.0142</li>
        <li><svg viewBox="0 0 12 12"><rect x="1" y="2.5" width="10" height="7" fill="var(--ink-white)"/><path d="M1 2.5 L6 6.5 L11 2.5" fill="none" stroke="var(--card-black)" stroke-width="1"/></svg>info@cedarridgemech.com</li>
        <li><svg viewBox="0 0 12 12"><circle cx="6" cy="6" r="5" fill="none" stroke="var(--ink-white)" stroke-width="1.2"/><ellipse cx="6" cy="6" rx="2.2" ry="5" fill="none" stroke="var(--ink-white)" stroke-width="1"/><line x1="1" y1="6" x2="11" y2="6" stroke="var(--ink-white)" stroke-width="1"/></svg>www.cedarridgemech.com</li>
      </ul>
    </div>
    <div class="brand-mark"><span class="brand-square"></span><span>Cedar Ridge Mechanical</span></div>
  </section>

  <section class="card card-back">
    <div class="brand-mark"><span class="brand-square"></span><span>Cedar Ridge Mechanical</span></div>
  </section>
</main>
</body>
</html>
```